Home Inspection Flyer

Looking to have flyer designed that features our business, services, and our contact information. There are three of us. We are all business partners and do not have a company phone number. So each of us would need to be listed on flyer along with our individual phone number. Everything you could possibly need is on our website from logo to services and contact information. https://brightmeadowhomereview.com/. If you could possible incorporate our company colors that would be great. You can find those in our logo top left hand side of website and attached. Please also include our proveritas and hobe logos ( home inspector affiliations ) on brochure as well. Those can be found on website. Please feel free to reach out with any questions.
Thanks
Dale
Updates
Looking to get a few tri fold designs. All the ones submitted have been 8x11
Look and feel

```html
<!DOCTYPE html>
<html lang="en">
<head>
<meta charset="utf-8">
<title>Brightmeadow Home Review – Home Buyer Inspection Flyer</title>
<link href="https://fonts.googleapis.com/css2?family=Arimo:wght@400;700&family=Roboto:wght@400;500&display=swap" rel="stylesheet">
<style>
  :root{
    --green:#7dc242;
    --purple:#6f3a96;
    --ink:#141414;
    --grey:#8a8a8a;
    --stage:#ffffff;
    --paper:#ffffff;
  }
  *{margin:0;padding:0;box-sizing:border-box}
  html,body{width:1200px;height:1200px;overflow:hidden;background:var(--stage)}
  body{position:relative;font-family:"Arimo",Arial,sans-serif;color:var(--ink)}
  .flyer{position:absolute;left:201px;top:81px;width:805px;height:1044px;background:var(--paper);
    box-shadow:0 2px 10px rgba(0,0,0,.18);overflow:hidden}
  .abs{position:absolute}

  .brand{left:41px;top:40px;display:flex;align-items:center;gap:8px}
  .brand-mark{width:14px;height:14px;background:var(--green)}
  .brand-name{font-weight:700;font-size:17px;line-height:1.15;color:var(--ink);width:150px}

  .hero-photo{left:361px;top:0;width:444px;height:350px;
    background:radial-gradient(ellipse at 65% 45%,#d9d2c6 0%,#c9b6a0 25%,#b9cde3 55%,rgba(255,255,255,0) 78%),
               linear-gradient(180deg,#a9c4e2 0%,#dfe8f2 50%,#ffffff 100%);
    -webkit-mask-image:linear-gradient(90deg,transparent 0%,#000 22%);mask-image:linear-gradient(90deg,transparent 0%,#000 22%)}

  .title-top{left:28px;top:130px;font-weight:700;font-size:47px;color:var(--green);letter-spacing:.3px}
  .title-band{left:26px;top:192px;width:431px;height:50px;background:var(--purple);color:#fff;
    font-weight:700;font-size:36px;line-height:50px;padding-left:11px;letter-spacing:.3px}
  .intro{left:26px;top:253px;width:380px;font-family:"Roboto",Arial,sans-serif;font-size:18.5px;line-height:19.6px;color:var(--grey)}
  .intro strong{color:var(--ink);font-family:"Arimo",Arial,sans-serif;font-weight:700}
  .intro .price{color:var(--green);font-weight:500}

  .green-band{left:26px;top:336px;width:502px;height:41px;background:var(--green);color:#fff;
    font-weight:700;font-size:23px;line-height:41px;padding-left:9px}

  .partner{top:410px;width:240px;text-align:center}
  .headshot{display:block;margin:0 auto;width:95px;height:95px;border-radius:50%;border:3px solid var(--green);
    background:radial-gradient(circle at 50% 40%,#b8a79a 0%,#8d8078 40%,#3a3a3a 100%)}
  .partner-name{margin-top:7px;font-family:"Roboto",Arial,sans-serif;font-size:19px;color:var(--purple)}
  .partner-role{font-weight:700;font-size:15.5px;line-height:15.5px;margin-top:3px;height:32px}
  .partner-phone{margin-top:4px;display:flex;justify-content:center;align-items:center;gap:8px;
    font-weight:700;font-size:25px;color:var(--green)}
  .partner-email{margin-top:6px;display:flex;justify-content:center;align-items:center;gap:9px;font-size:13.5px}

  .purple-band{left:26px;top:670px;width:676px;height:52px;background:var(--purple);color:#fff;
    font-weight:700;font-size:23px;line-height:52px;padding-left:7px;letter-spacing:.2px}

  .benefits{list-style:none;font-size:16px}
  .benefits li{display:flex;align-items:flex-start;gap:14px;line-height:19px}
  .benefits svg{flex:none;margin-top:1px}
  .benefits.left{left:26px;top:743px}
  .benefits.left li{height:35.4px}
  .benefits.left li:last-child{height:auto}
  .benefits.left li:nth-child(6){height:30px}
  .benefits.right{left:424px;top:743px;width:340px}
  .benefits.right li{min-height:35.4px}

  .schedule{left:71px;top:991px;height:38px;display:flex;align-items:center;font-family:"Roboto",Arial,sans-serif;font-size:21px}
  .schedule .label{color:var(--green);margin-right:6px}
  .hours{left:486px;top:991px;width:215px;height:38px;background:var(--purple);color:#fff;
    font-weight:700;font-size:31px;line-height:38px;text-align:center}
</style>
</head>
<body>
<main class="flyer">
  <div class="abs brand"><span class="brand-mark"></span><span class="brand-name">Brightmeadow Home Review</span></div>

  <div class="abs hero-photo" role="img" aria-label="Photo of a two-storey house with a hand holding a magnifying glass over it"></div>

  <h1 class="abs title-top">Home Buyer</h1>
  <div class="abs title-band">Inspection Residential</div>
  <p class="abs intro"><strong>Pittsburgh's</strong> Preferred Home Inspection Service. Complete Home Inspection <span class="price">Starting at $350</span>. No Hidden Charges.</p>

  <div class="abs green-band">Pittsburgh's Top-Rated Home Inspectors</div>

  <section class="abs partner" style="left:30px">
    <span class="headshot" role="img" aria-label="Headshot of Owen Hartley"></span>
    <div class="partner-name">Owen Hartley</div>
    <div class="partner-role">Co-Owner &amp; Principal<br>Partner</div>
    <div class="partner-phone"><svg width="14" height="22" viewBox="0 0 14 22"><rect x="1.5" y="1.5" width="11" height="19" rx="2" fill="none" stroke="#7dc242" stroke-width="2.2"/><line x1="5" y1="17" x2="9" y2="17" stroke="#7dc242" stroke-width="2"/></svg>(412) 555-0142</div>
    <div class="partner-email"><svg width="22" height="20" viewBox="0 0 22 20"><path d="M21 1 1 9l7 2 2 8 3-6 5 3z" fill="#6f3a96"/></svg>brightmeadowowen@mailbox.com</div>
  </section>

  <section class="abs partner" style="left:274px">
    <span class="headshot" role="img" aria-label="Headshot of Dale Korvan"></span>
    <div class="partner-name">Dale Korvan</div>
    <div class="partner-role">Certified Home Inspector<br>&amp; Building Consultant</div>
    <div class="partner-phone"><svg width="14" height="22" viewBox="0 0 14 22"><rect x="1.5" y="1.5" width="11" height="19" rx="2" fill="none" stroke="#7dc242" stroke-width="2.2"/><line x1="5" y1="17" x2="9" y2="17" stroke="#7dc242" stroke-width="2"/></svg>(412) 555-0187</div>
    <div class="partner-email"><svg width="22" height="20" viewBox="0 0 22 20"><path d="M21 1 1 9l7 2 2 8 3-6 5 3z" fill="#6f3a96"/></svg>brightmeadowdale@mailbox.com</div>
  </section>

  <section class="abs partner" style="left:535px">
    <span class="headshot" role="img" aria-label="Headshot of Ellis Brandt"></span>
    <div class="partner-name">Ellis Brandt</div>
    <div class="partner-role">Co-Owner &amp; Principal<br>Partner</div>
    <div class="partner-phone"><svg width="14" height="22" viewBox="0 0 14 22"><rect x="1.5" y="1.5" width="11" height="19" rx="2" fill="none" stroke="#7dc242" stroke-width="2.2"/><line x1="5" y1="17" x2="9" y2="17" stroke="#7dc242" stroke-width="2"/></svg>(724) 555-0126</div>
    <div class="partner-email"><svg width="22" height="20" viewBox="0 0 22 20"><path d="M21 1 1 9l7 2 2 8 3-6 5 3z" fill="#6f3a96"/></svg>brightmeadowellis@mailbox.com</div>
  </section>

  <div class="abs purple-band">Brightmeadow Home Review's Benefits &amp; Credentials</div>

  <ul class="abs benefits left">
    <li><svg width="20" height="16" viewBox="0 0 20 16"><path d="M2 8l6 6L18 2" fill="none" stroke="#7dc242" stroke-width="2.6"/></svg>Fast, Reliable, Affordable Pricing</li>
    <li><svg width="20" height="16" viewBox="0 0 20 16"><path d="M2 8l6 6L18 2" fill="none" stroke="#7dc242" stroke-width="2.6"/></svg>Available On Evenings And Weekends</li>
    <li><svg width="20" height="16" viewBox="0 0 20 16"><path d="M2 8l6 6L18 2" fill="none" stroke="#7dc242" stroke-width="2.6"/></svg>Agent - Relator Access Keys</li>
    <li><svg width="20" height="16" viewBox="0 0 20 16"><path d="M2 8l6 6L18 2" fill="none" stroke="#7dc242" stroke-width="2.6"/></svg>48 Hour Reporting</li>
    <li><svg width="20" height="16" viewBox="0 0 20 16"><path d="M2 8l6 6L18 2" fill="none" stroke="#7dc242" stroke-width="2.6"/></svg>Licensed By State Of Pennsylvania</li>
    <li><svg width="20" height="16" viewBox="0 0 20 16"><path d="M2 8l6 6L18 2" fill="none" stroke="#7dc242" stroke-width="2.6"/></svg>Members Of Home Observers Board Of Excellence</li>
    <li><svg width="20" height="16" viewBox="0 0 20 16"><path d="M2 8l6 6L18 2" fill="none" stroke="#7dc242" stroke-width="2.6"/></svg>Continuous Learning And Professional Development</li>
  </ul>

  <ul class="abs benefits right">
    <li><svg width="20" height="16" viewBox="0 0 20 16"><path d="M2 8l6 6L18 2" fill="none" stroke="#7dc242" stroke-width="2.6"/></svg>Abide By The HOBE Code Of Ethics</li>
    <li><svg width="20" height="16" viewBox="0 0 20 16"><path d="M2 8l6 6L18 2" fill="none" stroke="#7dc242" stroke-width="2.6"/></svg>Professional Level Of Liability Insurance</li>
    <li><svg width="20" height="16" viewBox="0 0 20 16"><path d="M2 8l6 6L18 2" fill="none" stroke="#7dc242" stroke-width="2.6"/></svg>Nationally Accredited B.S. Business &amp;<br>Marketing Degrees</li>
    <li><svg width="20" height="16" viewBox="0 0 20 16"><path d="M2 8l6 6L18 2" fill="none" stroke="#7dc242" stroke-width="2.6"/></svg>Additional Services Available</li>
  </ul>

  <p class="abs schedule"><span class="label">Flexible Scheduling:</span>7 Days A Week From</p>
  <div class="abs hours">7:00a – 9:00p</div>
</main>
</body>
</html>
```